Verlindo Magician

I want the business card for my business to give to people who watch that later I will be employed to show magic here is my website http://www.balsamomagicien.com/I want the interesting design , i am very opened for formal and informal, I watch a lot of design so don't stick to the common shape and form but i hope it can also be produced the thing to write on will be the same as in picture that i will upload , i also will upload the logo for you that so can be easy to useDenis CostilleMagicianMAGICIAN VERLINDO 17 rue des Tilleuls - 25000 BESANÇON contact@verlindoillusions.example tel. 0381 946 157 tel. 0674 219 503

```html
<!DOCTYPE html>
<html lang="fr">
<head>
<meta charset="utf-8">
<title>Verlindo Magician – Business Card</title>
<link rel="stylesheet" href="https://fonts.googleapis.com/css2?family=Source+Sans+3:wght@400;600&display=swap">
<style>
  :root {
    --backdrop: #5c5c5c;
    --card: #ffffff;
    --ink: #111111;
    --accent: #c8201e;
    --figure-dark: #0d0d0d;
    --figure-mid: #3a3a3a;
  }
  * { box-sizing: border-box; margin: 0; padding: 0; }
  html, body {
    width: 1200px; height: 802px; overflow: hidden;
    background: var(--backdrop);
    font-family: "Source Sans 3", "Myriad Pro", Arial, sans-serif;
    color: var(--ink);
  }
  .card {
    position: absolute; top: 274px;
    width: 442px; height: 265px;
    background: var(--card);
    overflow: hidden;
  }
  .card--front { left: 136px; }
  .card--back  { left: 624px; }

  .portrait-area {
    position: absolute; left: 0; top: 0;
    width: 196px; height: 100%;
    background: linear-gradient(160deg, var(--figure-dark) 0%, var(--figure-mid) 60%, var(--figure-dark) 100%);
  }

  .details {
    position: absolute; right: 21px; top: 0;
    text-align: right; line-height: 1;
  }
  .details__name {
    position: absolute; right: 0; top: 41px; white-space: nowrap;
    font-size: 16.5px; font-weight: 600; color: var(--accent); letter-spacing: 0.2px;
  }
  .details__role {
    position: absolute; right: 5px; top: 59px; white-space: nowrap;
    font-size: 11.5px;
  }
  .details__company {
    position: absolute; right: 0; top: 121px; white-space: nowrap;
    font-size: 11.5px; font-weight: 600; color: var(--accent);
  }
  .details__line {
    position: absolute; right: 0; white-space: nowrap;
    font-size: 11.5px;
  }
  .contact {
    position: absolute; right: 0; white-space: nowrap;
    font-size: 11.5px; display: flex; align-items: center; gap: 6px;
  }
  .contact svg { width: 10px; height: 10px; fill: var(--accent); flex: none; }

  .brand {
    position: absolute; left: 0; right: 0; top: 50%;
    transform: translateY(-50%);
    text-align: center; color: var(--ink); font-weight: 400;
  }
  .brand__name {
    font-size: 28px; letter-spacing: 1px; line-height: 1;
  }
  .brand__tagline {
    margin-top: 4px;
    font-size: 9px; letter-spacing: 0.5px; line-height: 1;
  }
</style>
</head>
<body>

<section class="card card--front">
  <div class="portrait-area" role="img" aria-label="Black and white illustration of the magician in a dark jacket holding a playing card"></div>

  <div class="details">
    <p class="details__name">MARC RAVOULET</p>
    <p class="details__role">Magician</p>
    <p class="details__company">MAGICIAN VERLINDO</p>
    <p class="details__line" style="top:137px">17 rue des Tilleuls - 25000</p>
    <p class="details__line" style="top:153px">BESANÇON</p>

    <p class="contact" style="top:183px">0381 946 157
      <svg viewBox="0 0 24 24" aria-hidden="true"><path d="M2 9c0-3 5-5 10-5s10 2 10 5v2h-5V9c-1-1-3-1.5-5-1.5S8 8 7 9v2H2z M5 13h14l2 8H3z"/></svg>
    </p>
    <p class="contact" style="top:199px">0674 219 503
      <svg viewBox="0 0 24 24" aria-hidden="true"><path d="M2 9c0-3 5-5 10-5s10 2 10 5v2h-5V9c-1-1-3-1.5-5-1.5S8 8 7 9v2H2z M5 13h14l2 8H3z"/></svg>
    </p>
    <p class="contact" style="top:215px">contact@verlindoillusions.example
      <svg viewBox="0 0 24 24" aria-hidden="true"><path d="M1 4h22v16H1z M3 6v1l9 6 9-6V6l-9 6z" fill-rule="evenodd"/></svg>
    </p>
    <p class="contact" style="top:231px">www.verlindoillusions.example
      <svg viewBox="0 0 24 24" aria-hidden="true"><circle cx="12" cy="12" r="11"/><path d="M6 8c2 0 3 1 3 3s2 2 2 4-1 3-1 5M15 4c0 2 2 3 4 3" stroke="#fff" stroke-width="1.6" fill="none"/></svg>
    </p>
  </div>
</section>

<section class="card card--back">
  <div class="brand">
    <p class="brand__name">VERLINDO</p>
    <p class="brand__tagline">MAGICIEN</p>
  </div>
</section>

</body>
</html>
```